Kickbut Home Page Design built to Sell

We need a new home page layout. The website is working now but we need a refresh. Our business has slowed down since a few years ago. We need to show we build ecommerce and membership websites. Here is the page now: https://www.brelvoxstudio.graphics/new-home/

Target Market(s)

Women, solopreneurs, artists, politicians

Industry/Entity Type

Design Agency

Number of Pages Required

1 page

Font styles to use
Sans Serif

Colors
b8a6cd
fabb94
acd136
00a990

Requirements
Must have
• Video header
Section for text and Step process similar to this website: https://quintarelweb.com/ [This is out sister company]
Places for images.
Call to action lead gen form and Get a quote.
The menu should show WEB, PRINT, VIDEO
Nice to have
• I LOVE this company: https://tarnwickly.com/guide/
Area for testimonials
Should not have
• We don't want a duplicate of https://quintarelweb.com/

```html
<!DOCTYPE html>
<html lang="en">
<head>
<meta charset="utf-8">
<title>Brelvoxstudio — Web Design Agency</title>
<link rel="stylesheet" href="https://fonts.googleapis.com/css2?family=Montserrat:wght@400;500;600&display=swap">
<style>
:root{
  --teal:#1f9a80;
  --teal-panel:#2a9e86;
  --lilac:#b8a6cd;
  --lilac-btn:#b393d3;
  --ink:#333;
  --ink-soft:#555;
  --white:#fff;
  --footer:#121212;
}
*{margin:0;padding:0;box-sizing:border-box}
html,body{width:1200px;height:2637px;overflow:hidden}
body{font-family:"Montserrat",sans-serif;color:var(--ink);position:relative;background:#fff}
.abs{position:absolute}
.btn{position:absolute;display:flex;align-items:center;justify-content:center;color:#fff;font-weight:500;border-radius:2px}

/* hero */
.hero{left:0;top:0;width:1200px;height:640px;background:linear-gradient(180deg,#2b2a33 0%,#4a4650 30%,#6b7342 70%,#7f9a3a 100%)}
.hero-media{left:0;top:0;width:1200px;height:640px;background:radial-gradient(ellipse at 78% 45%,rgba(220,225,235,.35),rgba(0,0,0,0) 55%)}
.logo{left:111px;top:24px;color:#fff}
.logo-name{font-size:31px;font-weight:600;letter-spacing:0;line-height:34px}
.logo-tag{font-size:9px;letter-spacing:1.6px;font-weight:500;margin-top:4px}
.nav{top:40px;left:735px;display:flex;gap:27px;color:#fff;font-size:13px;font-weight:500;letter-spacing:.5px}
.hero-quote{left:955px;top:32px;width:133px;height:33px;background:var(--lilac-btn);font-size:13px}
.hero-title{left:111px;top:300px;color:#fff;font-size:22px;line-height:37px;font-weight:400}
.play-now{left:111px;top:388px;color:#fff;font-size:18px;font-style:italic;text-decoration:underline}

/* agency */
.h-top{font-size:31px;font-weight:400;letter-spacing:1px;color:var(--ink)}
.h-accent{font-size:31px;font-weight:500;letter-spacing:1px;color:var(--teal)}
.body-copy{font-size:13px;line-height:19px;color:var(--ink-soft)}
.agency-text{left:110px;top:692px;width:445px}
.agency-text .body-copy{margin-top:20px}
.agency-btn{left:110px;top:993px;width:175px;height:33px;background:var(--teal);font-size:13px}
.illus{left:723px;top:640px;width:477px;height:324px;background:linear-gradient(135deg,#9fd3e0,#a8d6e2 55%,#f2c24a 80%,#8ecbdc)}
.photo-worker{left:598px;top:754px;width:362px;height:335px;background:linear-gradient(160deg,#4a4038,#7a6a5c 50%,#c8c2bb)}

/* process */
.photo-hands{left:0;top:1089px;width:598px;height:592px;background:linear-gradient(150deg,#6a5c52,#9aa4b4 45%,#3f8fd0 75%,#7fa6cf)}
.process-bg{left:598px;top:1089px;width:602px;height:592px;background:radial-gradient(circle at 90% 25%,rgba(236,200,220,.7),rgba(255,255,255,0) 45%),radial-gradient(circle at 20% 45%,rgba(170,225,215,.55),rgba(255,255,255,0) 45%),#fff}
.process-text{left:643px;top:1148px;width:440px}
.process-text .body-copy{margin-top:14px}
.step{position:absolute;left:649px;width:440px}
.step-num{position:absolute;left:0;top:0;width:40px;height:40px;border-radius:50%;background:var(--teal);color:#fff;font-weight:600;font-size:18px;display:flex;align-items:center;justify-content:center}
.step-title{position:absolute;left:56px;top:0;font-size:17px;font-weight:500;color:var(--ink)}
.step-copy{position:absolute;left:59px;top:24px;width:380px;font-size:11.5px;line-height:16px;color:var(--ink-soft)}
.process-btn{left:643px;top:1579px;width:176px;height:33px;background:var(--teal);font-size:13px}

/* quote */
.quote-text{left:110px;top:1738px;width:440px}
.quote-text .body-copy{margin-top:18px}
.quote-panel{left:598px;top:1681px;width:602px;height:360px;background:linear-gradient(160deg,#2f9f88,#259a80 60%,#1e8f76)}
.field{position:absolute;width:226px;height:33px;background:#fff;font-size:13px;color:#555;display:flex;align-items:center;padding-left:18px}
.field.select{justify-content:space-between;padding-right:16px;font-size:12px}
.quote-btn{left:914px;top:1912px;width:174px;height:33px;background:var(--lilac-btn);font-size:17px;letter-spacing:1px}

/* testimonial */
.testimonial{left:0;top:2041px;width:1200px;height:440px;background:var(--lilac)}
.client-photo{left:113px;top:2133px;width:250px;height:250px;border-radius:50%;background:radial-gradient(circle at 50% 60%,#cfd3da,#f4f4f4)}
.quote-mark{left:168px;top:2318px;font-size:90px;line-height:80px;color:#fff;font-weight:600}
.testi-head{left:425px;top:2160px;color:#fff;font-size:30px;letter-spacing:1px}
.testi-copy{left:425px;top:2212px;width:650px;color:#fff;font-size:13.5px;line-height:22.5px}
.testi-name{left:425px;top:2340px;color:#fff;font-size:22px;letter-spacing:1px}
.testi-role{left:425px;top:2376px;color:#fff;font-size:15px;letter-spacing:.5px}

/* footer */
.footer{left:0;top:2481px;width:1200px;height:156px;background:var(--footer);color:#fff}
.foot-nav{left:111px;top:2523px;display:flex;gap:27px;font-size:13px}
.socials{left:551px;top:2508px;display:flex;gap:6px}
.socials span{width:20px;height:20px;border-radius:50%;background:#fff}
.help{left:792px;top:2506px;font-size:13px;line-height:18px}
.phone{left:911px;top:2519px;font-size:24px;font-weight:500}
.foot-rule{left:113px;top:2556px;width:977px;height:1px;background:#777}
.copyright{left:113px;top:2583px;font-size:13px}
.email-label{left:758px;top:2588px;font-size:13px}
.email{left:836px;top:2583px;font-size:17px}
</style>
</head>
<body>

<section class="abs hero">
  <div class="abs hero-media" role="img" aria-label="Video header: desk with a large monitor, tablet and phone showing an online shop"></div>
  <div class="abs logo">
    <div class="logo-name">BRELVOXSTUDIO</div>
    <div class="logo-tag">GRAPHICS WEB VIDEO CONSULTANTS</div>
  </div>
  <nav class="abs nav"><span>WEB</span><span>PRINT</span><span>VIDEO</span></nav>
  <div class="btn hero-quote">Get a Quote</div>
  <svg class="abs" style="left:111px;top:244px" width="50" height="36" viewBox="0 0 50 36" aria-hidden="true">
    <rect x="2" y="2" width="46" height="32" rx="9" fill="none" stroke="#fff" stroke-width="3"/>
    <path d="M19 10 L33 18 L19 26 Z" fill="none" stroke="#fff" stroke-width="3" stroke-linejoin="round"/>
  </svg>
  <h1 class="abs hero-title" style="font-weight:400">LEAD GENERATING WEBSITES<br>THAT MOVE YOUR BUSINESS FORWARD</h1>
  <div class="abs play-now">PLAY NOW</div>
</section>

<section>
  <div class="abs agency-text">
    <div class="h-top">WE ARE A</div>
    <div class="h-accent">WEB DESIGN AGENCY</div>
    <p class="body-copy" style="margin-top:20px">We help brands sell online with beautifully designed websites and effective digital marketing strategies that deliver results &amp; help your business grow.</p>
    <p class="body-copy" style="margin-top:18px">Quintarel Designs is a New England web design agency providing high quality, professional and reliable website - webpage design and graphic design services to individuals, nonprofits, small - medium sized businesses, and political campaigns. We are a small team of highly professional web consultants with over 20 years of knowledge and experience and we'd love to help you too!</p>
  </div>
  <div class="btn agency-btn">Read More About Us</div>
  <div class="abs illus" role="img" aria-label="Illustration of code window, image card and alarm clock"></div>
  <div class="abs photo-worker" role="img" aria-label="Photo of a smiling woman working on a laptop"></div>
</section>

<section>
  <div class="abs photo-hands" role="img" aria-label="Photo of hands arranging website wireframe sketches"></div>
  <div class="abs process-bg"></div>
  <div class="abs process-text">
    <div class="h-top">QUINTAREL</div>
    <div class="h-accent">THE PROCESS IS SIMPLE</div>
    <p class="body-copy" style="margin-top:12px">We help brands sell online with beautifully designed websites and effective digital marketing strategies that deliver results &amp; help your business grow.</p>
  </div>
  <div class="step" style="top:1307px"><div class="step-num">01</div><div class="step-title">Sed ut perspiciatis unde omnis</div><div class="step-copy">Sed ut perspiciatis unde omnis iste natus error sit voluptatem accusantium doloremque laudantium, totam rem.</div></div>
  <div class="step" style="top:1394px"><div class="step-num">02</div><div class="step-title">Sed ut perspiciatis unde omnis</div><div class="step-copy">Sed ut perspiciatis unde omnis iste natus error sit voluptatem accusantium doloremque laudantium, totam rem.</div></div>
  <div class="step" style="top:1480px"><div class="step-num">03</div><div class="step-title">Sed ut perspiciatis unde omnis</div><div class="step-copy">Sed ut perspiciatis unde omnis iste natus error sit voluptatem accusantium doloremque laudantium, totam rem.</div></div>
  <div class="btn process-btn">Get A Free Quote</div>
</section>

<section>
  <div class="abs quote-text">
    <div class="h-top">GET A QUOTE</div>
    <div class="h-accent">WEBSITE PERFORMING?</div>
    <p class="body-copy" style="margin-top:20px">Sed ut perspiciatis unde omnis iste natus error sit voluptatem accusantium doloremque laudantium, totam rem aperiam, eaque ipsa quae ab illo inventore veritatis et quasi architecto beatae vitae dicta sunt explicabo.</p>
    <p class="body-copy" style="margin-top:18px">Nemo enim ipsam voluptatem quia voluptas sit aspernatur aut odit aut fugit, sed quia consequuntur magni dolores eos qui ratione</p>
  </div>
  <div class="abs quote-panel" role="img" aria-label="Teal-tinted photo of a team working in an office"></div>
  <div class="field" style="left:628px;top:1778px">First Name</div>
  <div class="field" style="left:862px;top:1778px">Last Name Name</div>
  <div class="field" style="left:628px;top:1822px">Phone</div>
  <div class="field" style="left:862px;top:1822px">Email</div>
  <div class="field" style="left:628px;top:1867px">Company Name</div>
  <div class="field select" style="left:862px;top:1867px">Select Your Services
    <svg width="10" height="7" viewBox="0 0 10 7" aria-hidden="true"><path d="M1 1 L5 5 L9 1" fill="none" stroke="#333" stroke-width="1.6"/></svg>
  </div>
  <div class="btn quote-btn">GET A QUOTE</div>
</section>

<section>
  <div class="abs testimonial"></div>
  <div class="abs client-photo" role="img" aria-label="Portrait photo of the client"></div>
  <div class="abs quote-mark">&ldquo;</div>
  <h2 class="abs testi-head" style="font-weight:400">WHY OUR CLIENTS LOVE US</h2>
  <p class="abs testi-copy">Dana Whitlock was great to work with and extremely knowledgeable and accessible. I especially appreciated his well thought out design process and the client videos he created to walk me through various stages of it. I received lots of great feedback on the visual look, user-friendliness, and rich content of my website throughout the campaign and was re-elected overwhelmingly. I highly recommend Dana and Quintarel Designs for your next project!</p>
  <div class="abs testi-name">-&nbsp;&nbsp;&nbsp;&nbsp;MARCUS EDENVALE</div>
  <div class="abs testi-role">MAYOR, HARLOW FALLS, VT</div>
</section>

<footer>
  <div class="abs footer"></div>
  <nav class="abs foot-nav"><span>WEB</span><span>PRINT</span><span>VIDEO</span></nav>
  <div class="abs socials" aria-label="Social links"><span></span><span></span><span></span><span></span></div>
  <div class="abs help">Need Help?<br>Call our Support:</div>
  <div class="abs phone">1-555-014-2290</div>
  <div class="abs foot-rule"></div>
  <div class="abs copyright">Quintarel Development © 2021.All Rights Reserved. |&nbsp; Privacy Policy</div>
  <div class="abs email-label">Email To:</div>
  <div class="abs email">hello@quintarelweb.com</div>
</footer>

</body>
</html>
```